Business Card for beauty technology startup

Design Glimora Business Card for a Beauty, based on the website identity and colors (https://www.glimora-example.com).
Glimora is a beauty tech startup that gathers helpful product info for beauty lovers and consumers (such as availability on stores, price range and product reviews) for makeup products. The card design must be young, colorful but clean, and very modern.

Target Market(s)

woman, 15-35

Industry/Entity Type

Cosmetics

Contact Information for Business Card

Full Name, address, phone

Font styles to use
Other font styles liked:
• Advent Pro

Colors
e34297
86cfc6
ffffff
5c5c5c
e8e8e8
e667a6
b2b2b2

Requirements
Must have
• One full colored side with a creative design and another with card info
• Use Color palette: #95C5C5 and/or #D38AA5
• Use fonts: Advent Pro
• Use website identity: https://www.glimora-example.com
Nice to have
• If needed extra font: Roboto

```html
<!DOCTYPE html>
<html lang="en">
<head>
<meta charset="utf-8">
<title>Glimora Business Card</title>
<link href="https://fonts.googleapis.com/css2?family=Advent+Pro:wght@300;400&family=Montserrat:wght@400&family=Roboto:wght@400;500&display=swap" rel="stylesheet">
<style>
  :root{
    --canvas:#e8e8e8;
    --rose:#be8497;
    --rose-line:#c999aa;
    --paper:#ffffff;
    --ink:#4e4247;
    --rule:#4a2f3a;
  }
  *{margin:0;padding:0;box-sizing:border-box}
  html,body{width:1200px;height:1155px;overflow:hidden;background:var(--canvas)}
  .card{position:absolute;left:218px;width:758px;height:434px;border-radius:32px;overflow:hidden}
  .card--front{top:134px;background:var(--rose)}
  .card--back{top:596px;background:var(--paper)}
  .front-name{position:absolute;inset:0;display:flex;align-items:center;justify-content:center;
    font-family:"Advent Pro",sans-serif;font-weight:300;font-size:96px;letter-spacing:10px;color:var(--paper)}
  .side-band{position:absolute;left:0;top:0;width:90px;height:100%;background:var(--rose)}
  .side-rule{position:absolute;left:95px;top:0;width:2px;height:100%;background:var(--rule)}
  .brand-dot{position:absolute;left:44px;top:40px;width:92px;height:92px;border-radius:50%;
    background:var(--paper);border:3px solid var(--rose)}
  .brand-name{position:absolute;left:164px;top:48px;font-family:"Advent Pro",sans-serif;font-weight:300;
    font-size:66px;letter-spacing:9px;line-height:1;color:var(--rose)}
  .person{position:absolute;right:46px;top:215px;text-align:right}
  .person-name{font-family:"Roboto",sans-serif;font-weight:500;font-size:29px;letter-spacing:0.5px;color:var(--rose);line-height:1}
  .person-role{margin-top:6px;font-family:"Roboto",sans-serif;font-size:15px;letter-spacing:1px;color:var(--ink)}
  .divider{position:absolute;left:165px;right:46px;top:279px;height:2px;background:var(--rose-line)}
  .contact{position:absolute;left:165px;top:308px;list-style:none;font-family:"Montserrat",sans-serif;font-size:19px;color:var(--ink)}
  .contact li{display:flex;align-items:center;height:27.5px}
  .contact svg{width:14px;height:14px;margin-right:17px;fill:none;stroke:var(--rose);stroke-width:1.6}
  .address{position:absolute;right:46px;top:336px;text-align:right;font-family:"Montserrat",sans-serif;font-size:19px;line-height:27.5px;color:var(--ink)}
</style>
</head>
<body>
  <section class="card card--front">
    <div class="front-name">Glimora</div>
  </section>

  <section class="card card--back">
    <div class="side-band"></div>
    <div class="side-rule"></div>
    <div class="brand-dot"></div>
    <div class="brand-name">GLIMORA</div>

    <div class="person">
      <div class="person-name">DANA WHITFIELD</div>
      <div class="person-role">OWNER</div>
    </div>
    <div class="divider"></div>

    <ul class="contact">
      <li><svg viewBox="0 0 14 14"><path d="M3 1.5l2 2.5-1.2 1.5c.8 1.8 2 3 3.8 3.8L9 8l2.5 2-1 2c-4.5-.3-8.2-4-8.5-8.5z"/></svg>555.014.2290</li>
      <li><svg viewBox="0 0 14 14"><rect x="1.5" y="3" width="11" height="8" rx="1"/><path d="M1.5 3.5L7 8l5.5-4.5"/></svg>info@glimora-example.com</li>
      <li><svg viewBox="0 0 14 14"><circle cx="7" cy="7" r="5.5"/><path d="M1.5 7h11M7 1.5c-2.5 3-2.5 8 0 11M7 1.5c2.5 3 2.5 8 0 11"/></svg>www.glimora-example.com</li>
    </ul>

    <div class="address">48 Palm Row<br>Seabrook, FL 33000</div>
  </section>
</body>
</html>
```